Mens Jewellery Homepage - Modern, Stylish Mens Ring Brand - Homepage

Project Overview: KestrelHoops.com is a men's accessories brand specializing in high-quality mens rings.

The objective of this redesign is to create a modern, visually appealing homepage that is easy to navigate, showcases a wide range of rings, highlights personalization options, and builds trust with customers.

The new design should make a strong impression while reflecting the brand's premium quality and commitment to craftsmanship.

The focus will be on a sleek aesthetic that aligns with the tastes of men shopping for wedding bands, engagement rings, or fashion accessories.

Objectives:

Modern and Sleek Aesthetic:

A clean, minimalist design that emphasizes high-quality product imagery and thoughtful use of space.
Contemporary color palette that conveys elegance and sophistication, with accents that highlight key elements without overwhelming the user.

Consistent and easy-to-read typography that reflects the brand’s modern and masculine identity.

Showcasing Products:
Hero Section: A image to show off 3 or 4 ring designs that could be used for weddings or fashion.

Product Highlights: Below the hero banner, showcase product categories by color (see current website for colors)

Featured Products: Display a selection of “Top Rated” or “Customer Favorites” rings to help guide users toward popular choices.

Personalization Section:
A dedicated section promoting the ability to personalize rings, emphasizing features like engraving with names, dates, or special messages.
Include lifestyle images of personalized rings to inspire customers and give them an idea of what’s possible.
Use callouts such as “Make It Yours” or “Personalize Your Ring” to encourage users to explore the customization options available for each product.

Building Trust:

A space to show 5 or 6 testimonials and other trust elements

Symbols / text to show

free delivery
free returns
every ring stock
fast delivery
customer images (from reviews)

Driving Conversions:
Include a prominent call-to-action (CTA) button in the hero section with text like “Shop Now” or “Discover Our Collections.”

User Experience:
Fast, easy-to-navigate layout with simple and intuitive categories. Product categories and main sections should be clearly visible and easy to access without overwhelming the user.
Design the homepage to feel cohesive and uncluttered, with a logical flow from product discovery to personalization and checkout.

Visual Elements and Imagery:
Use ring images from our site, but add backgrounds etc to make the image on the homepage more interesting.

Personalization Options: Use visual representations (like ring mockups) showing where personalization options (such as engravings) would appear on the product.

I like (and would like to see some different designs from our current design)
Vorm.com for design
ridgeloops.com

Target Market(s)

Men - 20 to 35

Number of Pages Required

1 page

Requirements
Must have
• Easy navigation, Trust, Modern, Clean,
Nice to have
• Would like to see Different designs like Vorm.com - RidgeLoops.com

```html
<!DOCTYPE html>
<html lang="en">
<head>
<meta charset="utf-8">
<title>Kestrel Hoops – Handcrafted Men's Rings</title>
<link href="https://fonts.googleapis.com/css2?family=Montserrat:wght@600;700;800&family=Poppins:wght@400;500;600;700&family=Great+Vibes&display=swap" rel="stylesheet">
<style>
:root{
  --ink:#111111;
  --ink-soft:#3a3a3a;
  --muted:#6b6b6b;
  --mint:#72d3b6;
  --mint-dark:#2f9e7f;
  --gold:#c9a23a;
  --gold-soft:#e6c769;
  --cream:#f1e3b5;
  --panel:#f4f4f4;
  --sun:#f5c93e;
  --white:#ffffff;
}
*{box-sizing:border-box;margin:0;padding:0}
html,body{width:1200px;height:4471px;overflow:hidden}
body{font-family:"Poppins",sans-serif;color:var(--ink);background:var(--white);position:relative}
.heading{font-family:"Montserrat",sans-serif;font-weight:800;text-transform:uppercase;letter-spacing:.5px}
.rule{width:200px;height:2px;margin:14px auto 0;background:linear-gradient(90deg,transparent,var(--gold),transparent)}
.btn{display:inline-block;font-weight:600;font-size:11px;text-transform:uppercase;border-radius:30px;letter-spacing:.5px}
.btn-mint{background:var(--mint);color:var(--ink);border:3px solid #fff;box-shadow:0 0 0 1px var(--mint)}

/* announcement + nav */
.announce{height:28px;background:var(--ink);color:#fff;font-size:10px;font-weight:500;display:flex;align-items:center;justify-content:center;gap:8px;text-transform:uppercase}
.nav{height:57px;display:flex;align-items:center;padding:0 36px;border-bottom:1px solid #eee}
.brand{display:flex;align-items:center;gap:8px;font-weight:600;font-size:13px;letter-spacing:4px}
.brand .mark{width:36px;height:36px;border:2px solid var(--ink);border-radius:50%}
.brand small{display:block;font-size:7px;letter-spacing:6px}
.nav-links{display:flex;gap:28px;margin-left:56px;font-size:10px;font-weight:500;text-transform:uppercase}
.nav-icons{margin-left:auto;display:flex;gap:14px}

/* hero */
.hero{height:421px;position:relative;background:linear-gradient(100deg,#2a2420 0%,#4a3d34 35%,#8a7766 65%,#5b4a3e 100%)}
.hero-media{position:absolute;right:120px;top:90px;width:360px;height:440px;border-radius:50%;background:radial-gradient(circle at 50% 45%,#f3d27a 0%,#d9a6a0 35%,#c9c9c9 60%,transparent 72%);opacity:.85}
.hero-copy{position:absolute;left:120px;top:80px;color:#fff}
.hero-copy .script{font-family:"Great Vibes",cursive;font-size:70px;color:var(--gold-soft);line-height:.8}
.hero-copy h1{font-family:"Montserrat",sans-serif;font-weight:800;font-size:44px;line-height:1}
.hero-copy p{font-size:13px;letter-spacing:1.2px;text-transform:uppercase;margin-top:10px;line-height:1.6}
.rating{font-size:10px;margin-top:10px;display:flex;gap:6px;align-items:center}
.rating .stars{color:var(--gold-soft);font-size:14px}
.hero .btn{margin-top:22px;padding:11px 30px}
.hero-dots{position:absolute;left:120px;bottom:18px;display:flex;gap:7px}
.hero-dots i{width:6px;height:6px;border-radius:50%;background:#ccc}
.hero-dots i:first-child{background:var(--gold-soft)}

/* browse by color */
.browse{padding-top:126px;height:1497px-506px}
.section-title{text-align:center;font-size:38px}
.color-grid{position:absolute;top:733px;left:118px;display:grid;grid-template-columns:repeat(3,301px);column-gap:30px;row-gap:33px}
.color-card{height:318px;border-radius:6px;background:radial-gradient(circle at 50% 60%,#2d2d2d,#050505);color:#fff;text-align:center;padding-top:30px;position:relative}
.color-card.silver{background:radial-gradient(circle at 50% 55%,#fafafa,#d6d6d6);color:var(--ink)}
.color-card h3{font-family:"Montserrat",sans-serif;font-size:18px;font-weight:700;text-transform:uppercase}
.color-card .bar{width:80px;height:2px;margin:10px auto 14px;background:linear-gradient(90deg,transparent,var(--gold),transparent)}
.color-card .tags{font-size:11px;text-transform:uppercase;letter-spacing:.6px}
.color-card .rings{width:250px;height:90px;margin:26px auto 0;border-radius:45px}
.color-card .btn{position:absolute;left:50%;transform:translateX(-50%);bottom:26px;padding:5px 20px;font-size:9px}
.color-card.silver .btn{background:var(--ink);color:#fff;box-shadow:0 0 0 1px var(--ink)}

/* favorites */
.favorites{position:absolute;top:1497px;left:0;width:1200px;height:643px;background:var(--panel);padding-top:85px}
.products{position:absolute;top:188px;left:118px;display:flex;gap:14px}
.product{width:230px;height:330px;background:#fff;border:1px solid #e6e6e6;border-radius:4px;text-align:center;position:relative}
.product .shot{width:130px;height:150px;margin:38px auto 0;border-radius:50%}
.product .price{font-weight:700;font-size:14px;margin-top:12px}
.product .name{font-size:12px;color:var(--ink-soft);line-height:1.35;margin-top:4px;padding:0 40px}
.product .cart{position:absolute;left:0;right:0;bottom:0;height:44px;background:var(--cream);font-size:10px;font-weight:600;text-transform:uppercase;display:flex;align-items:center;justify-content:center}
.product.active .cart{background:var(--mint)}
.arrow{position:absolute;top:340px;width:36px;height:36px;border-radius:50%;background:#d9d9d9;display:flex;align-items:center;justify-content:center}
.arrow.l{left:47px}.arrow.r{right:47px;background:#fff;border:1px solid #ddd}
.pager{position:absolute;left:50%;transform:translateX(-50%);display:flex;gap:5px}
.pager i{width:16px;height:2px;background:#cfcfcf}
.pager i.on{background:var(--ink)}

/* personalize */
.personalize{position:absolute;top:2140px;left:0;width:1200px;height:716px;padding-top:90px}
.photo-frame{position:absolute;left:118px;top:201px;width:407px;height:391px;border:4px solid var(--ink);border-radius:10px;padding:10px}
.photo-frame .fill{width:100%;height:100%;border-radius:6px;background:linear-gradient(135deg,#6f4f3c,#c98f70 45%,#8e624a)}
.photo-rings{position:absolute;left:448px;top:516px;width:150px;height:130px;border-radius:50%;background:radial-gradient(circle,#f1cf59,#c7c7c7 55%,transparent 70%)}
.make{position:absolute;left:664px;top:222px;width:400px}
.make h3{font-size:28px;font-weight:600}
.make .bar{width:80px;height:2px;background:var(--gold);margin:8px 0 20px}
.make p{font-size:11px;line-height:1.85;color:var(--ink-soft)}
.make ul{list-style:none;margin-top:16px}
.make li{display:flex;align-items:center;gap:10px;font-size:12px;font-weight:600;margin-bottom:13px}
.make .btn{margin-top:10px;padding:10px 30px}

/* trust band */
.trust{position:absolute;top:2856px;left:0;width:1200px;height:311px;background:radial-gradient(circle at 85% 30%,#3b3322,#0c0c0c 60%);display:flex;padding:0 90px;align-items:center;color:#fff}
.trust-item{flex:1;text-align:center;border-right:1px solid #333;padding:10px 0}
.trust-item:last-child{border-right:none}
.trust-item .ic{width:76px;height:76px;margin:0 auto 14px;border:2px solid var(--gold-soft);border-radius:50%;display:flex;align-items:center;justify-content:center}
.trust-item h4{font-size:15px;font-weight:600}
.trust-item span{font-size:10px;color:#ccc}

/* reviews */
.reviews{position:absolute;top:3167px;left:0;width:1200px;height:540px;padding-top:88px}
.review-row{position:absolute;top:189px;left:118px;display:flex;gap:33px}
.review{width:300px;height:222px;border:1px solid #e4e4e4;border-radius:4px;padding:24px 28px;position:relative;background:linear-gradient(135deg,#fff,#fafafa)}
.review .who{display:flex;align-items:center;gap:12px}
.avatar{width:62px;height:62px;border-radius:50%;border:3px solid var(--mint);background:linear-gradient(#e9d7c6,#b89a82)}
.who b{font-size:13px;font-weight:600;display:block}
.who em{font-style:normal;font-size:9px;color:var(--muted)}
.review p{font-size:10px;line-height:1.6;color:var(--ink-soft);margin-top:18px}
.review .stars{position:absolute;left:28px;bottom:22px;color:var(--gold);font-size:20px;letter-spacing:1px}
.review .quote{position:absolute;right:24px;bottom:12px;font-size:48px;color:#ddd;font-family:Georgia,serif;line-height:1}

/* exchange band */
.exchange{position:absolute;top:3707px;left:0;width:1200px;height:406px;background:linear-gradient(90deg,#f3c23a,#f7d45a 50%,#f3c23a);text-align:center;color:#fff;padding-top:104px}
.exchange h2{font-family:"Montserrat",sans-serif;font-weight:800;font-size:38px;line-height:1.1}
.exchange p{font-size:14px;letter-spacing:1.4px;margin-top:30px;line-height:1.4}
.exchange .btn{margin-top:22px;padding:11px 36px;background:#fff;color:var(--ink);border:3px solid var(--sun);box-shadow:0 0 0 2px #fff}

/* footer */
.footer{position:absolute;top:4127px;left:0;width:1200px;height:344px;background:#0d0d0d;color:#fff}
.footer .brand{position:absolute;left:118px;top:85px;color:#fff}
.footer .brand .mark{border-color:#fff;width:46px;height:46px}
.socials{position:absolute;left:145px;top:150px;display:flex;gap:13px}
.socials i{width:32px;height:32px;border:1px solid #888;border-radius:50%}
.fcol{position:absolute;top:95px}
.fcol h5{font-size:13px;font-weight:600;text-transform:uppercase;margin-bottom:16px}
.fcol a{display:block;font-size:10px;color:#ccc;text-decoration:none;margin-bottom:10px;text-transform:uppercase}
.fcol.services a{text-transform:none}
.contact div{display:flex;gap:12px;font-size:10px;color:#ccc;margin-bottom:20px;align-items:center}
.legal{position:absolute;left:118px;right:118px;top:298px;border-top:1px solid #444;padding-top:14px;font-size:9px;color:#bbb;display:flex;justify-content:space-between}
.cards{display:flex;gap:4px}
.cards i{width:32px;height:18px;border-radius:2px;background:#fff}
.cards i:nth-child(2){background:#4d7cc9}.cards i:nth-child(4){background:#3a3a3a}
</style>
</head>
<body>

<div class="announce">
  <svg width="18" height="12" viewBox="0 0 18 12" fill="none" stroke="#fff" stroke-width="1.4"><rect x="1" y="1" width="10" height="7"/><path d="M11 3h4l2 3v2h-6"/><circle cx="4" cy="10" r="1.4"/><circle cx="14" cy="10" r="1.4"/></svg>
  Free 1 to 2 day delivery and returns
</div>

<header class="nav">
  <div class="brand"><span class="mark"></span><span>KESTREL<small>HOOPS</small></span></div>
  <nav class="nav-links"><span>Home</span><span>Shop BT Material ▾</span><span>Shop by Color ▾</span><span>Personalize Rings</span><span>Try at Home</span></nav>
  <div class="nav-icons">
    <svg width="16" height="16" viewBox="0 0 16 16" fill="none" stroke="#111" stroke-width="1.6"><circle cx="7" cy="7" r="5"/><path d="M11 11l4 4"/></svg>
    <svg width="16" height="16" viewBox="0 0 16 16" fill="none" stroke="#111" stroke-width="1.6"><path d="M3 5h10l-1 10H4z"/><path d="M6 5V3a2 2 0 014 0v2"/></svg>
    <svg width="16" height="16" viewBox="0 0 16 16" fill="none" stroke="#111" stroke-width="1.6"><circle cx="8" cy="8" r="7"/><circle cx="8" cy="6" r="2.4"/><path d="M3.5 13c1.5-2.5 7.5-2.5 9 0"/></svg>
  </div>
</header>

<section class="hero">
  <div class="hero-media" role="img" aria-label="Gold, rose gold and silver wedding bands resting on a hand"></div>
  <div class="hero-copy">
    <div class="script">Elevate</div>
    <h1>YOUR STYLE</h1>
    <p>Handcrafted rings with free fast<br>delivery &amp; hassle free returns</p>
    <div class="rating"><span class="stars">★★★★★</span><b>4.9 / 5.0</b> Rating from <b>9,850 + Reviews</b></div>
    <a class="btn btn-mint">Shop Now</a>
  </div>
  <div class="hero-dots"><i></i><i></i><i></i><i></i></div>
</section>

<section class="browse">
  <h2 class="heading section-title">Browse by Color</h2>
  <div class="rule"></div>
</section>
<div class="color-grid">
  <div class="color-card"><h3>Black Collection</h3><div class="bar"></div><div class="tags">Strong | Fearless | Majestic</div><div class="rings" role="img" aria-label="Black, blue and copper rings" style="background:linear-gradient(90deg,#222,#555,#1f3f8a,#c07a4a)"></div><a class="btn btn-mint">Shop Now</a></div>
  <div class="color-card silver"><h3>Silver Collection</h3><div class="bar"></div><div class="tags">Calm | Sophisticated | Elegant</div><div class="rings" role="img" aria-label="Silver rings" style="background:linear-gradient(90deg,#9a9a9a,#e8e8e8,#6c7a9c,#cfcfcf)"></div><a class="btn">Shop Now</a></div>
  <div class="color-card"><h3>Blue Collection</h3><div class="bar"></div><div class="tags">Constant | Loyal | True</div><div class="rings" role="img" aria-label="Blue rings" style="background:linear-gradient(90deg,#1f4fa8,#5a8ad6,#2a5bbf,#1a3b80)"></div><a class="btn btn-mint">Shop Now</a></div>
  <div class="color-card"><h3>Gold Collection</h3><div class="bar"></div><div class="tags">Bright | Brilliant | Classic</div><div class="rings" role="img" aria-label="Gold rings" style="background:linear-gradient(90deg,#c99a2e,#f0d27a,#b8862a,#e0bd5a)"></div><a class="btn btn-mint">Shop Now</a></div>
  <div class="color-card"><h3>Brown Collection</h3><div class="bar"></div><div class="tags">Authentic | Genuine | Simple</div><div class="rings" role="img" aria-label="Wood inlay rings" style="background:linear-gradient(90deg,#5a3a2a,#8a3a4a,#a0603a,#6a4a3a)"></div><a class="btn btn-mint">Shop Now</a></div>
  <div class="color-card"><h3>Rose Gold Collection</h3><div class="bar"></div><div class="tags">Romantic | Vintage | Sublime</div><div class="rings" role="img" aria-label="Rose gold rings" style="background:linear-gradient(90deg,#c98a6a,#e8b89a,#b0b0b0,#d49a7a)"></div><a class="btn btn-mint">Shop Now</a></div>
</div>

<section class="favorites">
  <h2 class="heading section-title">Customer Favorites</h2>
  <div class="rule"></div>
  <div class="arrow l"><svg width="10" height="10" viewBox="0 0 10 10" fill="none" stroke="#333" stroke-width="1.5"><path d="M6 2L3 5l3 3"/></svg></div>
  <div class="products">
    <div class="product"><div class="shot" role="img" aria-label="Black and blue titanium ring" style="background:radial-gradient(circle,#fff 40%,#1a3fa0 45%,#111 62%,transparent 64%)"></div><div class="price">$45.00</div><div class="name">Black And Blue Titanium Rings</div><div class="cart">Add to Cart</div></div>
    <div class="product active"><div class="shot" role="img" aria-label="Brushed black ring" style="background:radial-gradient(circle,#fff 40%,#222 45%,#444 62%,transparent 64%)"></div><div class="price">$45.00</div><div class="name">Brushed Black Ring With Bevelled Sides</div><div class="cart">Add to Cart</div></div>
    <div class="product"><div class="shot" role="img" aria-label="Brushed silver ring" style="background:radial-gradient(circle,#fff 40%,#bdbdbd 45%,#8a8a8a 62%,transparent 64%)"></div><div class="price">$45.00</div><div class="name">Brushed Silver Ring</div><div class="cart">Add to Cart</div></div>
    <div class="product"><div class="shot" role="img" aria-label="Gold tungsten ring" style="background:radial-gradient(circle,#fff 40%,#f0cf5a 45%,#c99a2e 62%,transparent 64%)"></div><div class="price">$45.00</div><div class="name">Traditional Men's Gold Ring in Tungsten</div><div class="cart">Add to Cart</div></div>
  </div>
  <div class="arrow r"><svg width="10" height="10" viewBox="0 0 10 10" fill="none" stroke="#333" stroke-width="1.5"><path d="M4 2l3 3-3 3"/></svg></div>
  <div class="pager" style="top:548px"><i></i><i class="on"></i><i></i><i></i><i></i></div>
</section>

<section class="personalize">
  <h2 class="heading section-title">Personalize Your Ring</h2>
  <div class="rule"></div>
  <div class="photo-frame"><div class="fill" role="img" aria-label="Hands showing an engraved gold band"></div></div>
  <div class="photo-rings" role="img" aria-label="Pair of gold and silver engraved rings"></div>
  <div class="make">
    <h3>Make It Yours</h3>
    <div class="bar"></div>
    <p>Personalize your ring with a meaningful engraving, whether it's a name, special date, or a unique symbol. Add your personal touch to any style from our collection, with options for inner or outer band engravings. Choose your font, preview your custom design, and create a ring that tells your story.</p>
    <ul>
      <li><svg width="20" height="20" viewBox="0 0 20 20" fill="none" stroke="#2f9e7f" stroke-width="1.6"><circle cx="10" cy="10" r="8"/><path d="M6 10l3 3 6-7"/></svg>Add a Special Date or Name</li>
      <li><svg width="20" height="20" viewBox="0 0 20 20" fill="none" stroke="#2f9e7f" stroke-width="1.6"><circle cx="10" cy="10" r="8"/><path d="M6 10l3 3 6-7"/></svg>Add a Special messages</li>
      <li><svg width="20" height="20" viewBox="0 0 20 20" fill="none" stroke="#2f9e7f" stroke-width="1.6"><circle cx="10" cy="10" r="8"/><path d="M6 10l3 3 6-7"/></svg>Available in Every Style</li>
    </ul>
    <a class="btn btn-mint">Personalize Now</a>
  </div>
</section>

<section class="trust">
  <div class="trust-item"><div class="ic"><svg width="44" height="30" viewBox="0 0 44 30" fill="none" stroke="#e6c769" stroke-width="2"><rect x="2" y="4" width="24" height="16"/><path d="M26 9h9l6 6v5H26"/><circle cx="10" cy="24" r="3"/><circle cx="33" cy="24" r="3"/></svg></div><h4>FREE DELIVERY</h4><span>Free Shipping on All Orders</span></div>
  <div class="trust-item"><div class="ic"><svg width="36" height="36" viewBox="0 0 36 36" fill="none" stroke="#e6c769" stroke-width="2"><path d="M6 12l12-6 12 6v12l-12 6-12-6z"/><path d="M6 12l12 6 12-6M18 18v12"/></svg></div><h4>Free Returns</h4><span>30-Day Return Guarantee</span></div>
  <div class="trust-item"><div class="ic"><svg width="26" height="40" viewBox="0 0 26 40" fill="none" stroke="#e6c769" stroke-width="2"><ellipse cx="13" cy="20" rx="10" ry="17"/><ellipse cx="13" cy="20" rx="5" ry="12"/></svg></div><h4>Every Ring in Stock</h4><span>Ready to Ship</span></div>
  <div class="trust-item"><div class="ic"><svg width="40" height="30" viewBox="0 0 40 30" fill="none" stroke="#e6c769" stroke-width="2"><circle cx="24" cy="15" r="11"/><path d="M24 9v6l4 3M2 10h9M4 15h7M6 20h5"/></svg></div><h4>Fast Delivery</h4><span>Fast and Reliable Shipping</span></div>
</section>

<section class="reviews">
  <h2 class="heading section-title">Customer Reviews</h2>
  <div class="rule"></div>
  <div class="review-row">
    <div class="review"><div class="who"><div class="avatar" role="img" aria-label="Customer portrait"></div><div><b>~Tessa Marlow</b><em>Dartmouth, NS</em></div></div><p>The website was easy to navigate and order from, delivery was very fast and the customer service was great. The item is great quality and happy with the price. Highly recommend</p><div class="stars">★★★★★</div><div class="quote">”</div></div>
    <div class="review"><div class="who"><div class="avatar" role="img" aria-label="Customer portrait"></div><div><b>~Paula Brennick</b><em>Moncton, NB</em></div></div><p>Very efficient service &amp; excellent communication, would recommend this business.</p><div class="stars">★★★★★</div><div class="quote">”</div></div>
    <div class="review"><div class="who"><div class="avatar" role="img" aria-label="Customer portrait"></div><div><b>~Irene Dovall</b><em>Collingwood, ON</em></div></div><p>A super friendly and profession family run business! My queries were responded to almost instantly and I felt really looked after! Thanks so much for all your help</p><div class="stars">★★★★★</div><div class="quote">”</div></div>
  </div>
  <div class="pager" style="top:443px"><i></i><i class="on" style="background:var(--mint)"></i><i></i><i></i><i></i></div>
</section>

<section class="exchange" role="img" aria-label="Warm yellow backdrop with a hand wearing a ring">
  <h2>FREE EXCHANGES UNTIL YOU ARE<br>COMPLETELY SATISFIED</h2>
  <p>Don't know your ring size? We will send you a free men's ring sizer<br>Try at home option</p>
  <a class="btn">Try Now</a>
</section>

<footer class="footer">
  <div class="brand"><span class="mark"></span><span>KESTREL<small>HOOPS</small></span></div>
  <div class="socials"><i aria-label="Social profile"></i><i aria-label="Social profile"></i><i aria-label="Social profile"></i></div>
  <div class="fcol" style="left:408px"><h5>Quick Links</h5><a>Home</a><a>Shop BT Material</a><a>Shop by Color</a><a>Personalize Rings</a></div>
  <div class="fcol services" style="left:630px"><h5>Services</h5><a>FREE ring sizer</a><a>FREE Delivery</a><a>Returns and Exchanges</a><a>Try at Home</a><a>Ring Engraving</a></div>
  <div class="fcol contact" style="left:879px"><h5>Contact Us</h5>
    <div><svg width="12" height="10" viewBox="0 0 12 10" fill="#72d3b6"><path d="M0 0h12v10H0z"/><path d="M0 0l6 5 6-5" stroke="#0d0d0d" fill="none"/></svg>hello@kestrelhoops.com</div>
    <div><svg width="12" height="12" viewBox="0 0 12 12" fill="#72d3b6"><path d="M2 1h3l1 3-2 1a6 6 0 003 3l1-2 3 1v3c-6 0-10-4-10-10z"/></svg>01632 960418</div>
    <div><svg width="10" height="14" viewBox="0 0 10 14" fill="none" stroke="#72d3b6" stroke-width="1.6"><path d="M5 13S1 8 1 5a4 4 0 018 0c0 3-4 8-4 8z"/><circle cx="5" cy="5" r="1.4"/></svg>22B Quarry Lane, Elmsford, EL4 7QT</div>
  </div>
  <div class="legal"><span>©2024 Kestrel Hoops . All Rights Reserved.</span><div class="cards"><i></i><i></i><i></i><i></i></div></div>
</footer>

</body>
</html>
```